MRT Property - Business Cards

Looking for a business card & general letterhead, signage etc design for our new logo.

Colours:
000a20
0056a2
00b5ef
0088ce
68cef2

Fonts:
Poppins
Karla

Please keep look and feel of new brand - example in the zip package I sent.

```html
<!DOCTYPE html>
<html lang="en">
<head>
<meta charset="utf-8">
<title>MRT Property – Business Cards</title>
<link rel="stylesheet" href="https://fonts.googleapis.com/css2?family=Poppins:wght@400;500;600;700&display=swap">
<style>
  :root {
    --stage: #1b1b1d;
    --ink-deep: #000a20;
    --card-night: #1b2038;
    --brand-navy: #0a3a7a;
    --brand-blue: #0056a2;
    --brand-mid: #0088ce;
    --brand-sky: #00b5ef;
    --brand-pale: #68cef2;
    --paper: #f4f5f7;
    --text-dark: #1c2230;
    --text-light: #ffffff;
  }
  * { box-sizing: border-box; margin: 0; padding: 0; }
  html, body { width: 1200px; height: 852px; overflow: hidden; }
  body {
    background: var(--stage);
    font-family: "Poppins", sans-serif;
    position: relative;
  }
  .card {
    position: absolute;
    top: 283px;
    width: 500px;
    height: 286px;
    border-radius: 22px;
    overflow: hidden;
  }
  /* Back side */
  .card--back { left: 70px; background: var(--card-night); }
  .card--back .wordmark {
    position: absolute;
    left: 0; right: 0; top: 96px;
    text-align: center;
    font-size: 42px;
    font-weight: 700;
    color: var(--brand-blue);
    letter-spacing: 1px;
  }
  .card--back .web {
    position: absolute;
    left: 0; right: 0; top: 200px;
    text-align: center;
    font-size: 11px;
    letter-spacing: 7px;
    color: #c9cfdd;
  }
  .card--back .rule {
    position: absolute;
    left: 24px; right: 24px; top: 238px;
    height: 4px;
    background: var(--brand-mid);
  }
  /* Front side */
  .card--front { left: 630px; background: var(--paper); }
  .card--front .waves { position: absolute; inset: 0; }
  .card--front .wordmark {
    position: absolute;
    left: 34px; top: 104px;
    font-size: 32px;
    font-weight: 700;
    color: var(--brand-blue);
    letter-spacing: 0.5px;
  }
  .holder {
    position: absolute;
    right: 34px; top: 26px;
    text-align: right;
  }
  .holder .name {
    font-size: 17px;
    font-weight: 700;
    color: var(--brand-mid);
    line-height: 1.2;
  }
  .holder .role {
    font-size: 8.5px;
    color: var(--text-dark);
  }
  .contacts {
    position: absolute;
    right: 22px; top: 140px;
    list-style: none;
    text-align: right;
    color: var(--text-light);
    font-size: 11px;
    line-height: 19px;
  }
  .contacts li { display: flex; justify-content: flex-end; align-items: center; gap: 7px; }
  .contacts svg { width: 11px; height: 11px; fill: var(--text-light); }
  .contacts .spacer { width: 11px; }
</style>
</head>
<body>

<section class="card card--back" aria-label="Business card back">
  <div class="wordmark">MRT Property</div>
  <div class="web">www.mrtproperty.com</div>
  <div class="rule"></div>
</section>

<section class="card card--front" aria-label="Business card front">
  <svg class="waves" viewBox="0 0 500 286" aria-hidden="true">
    <path d="M500 100 C400 96 340 110 300 160 C260 215 200 244 0 256 L0 286 L500 286 Z" fill="var(--brand-navy)"/>
    <path d="M500 88 C400 84 335 98 290 150 C250 203 190 236 0 246" fill="none" stroke="var(--brand-mid)" stroke-width="5"/>
    <path d="M250 236 C200 256 120 264 0 270" fill="none" stroke="var(--brand-sky)" stroke-width="6"/>
  </svg>

  <div class="wordmark">MRT Property</div>

  <div class="holder">
    <div class="name">Callum Reid</div>
    <div class="role">Associate Director</div>
  </div>

  <ul class="contacts">
    <li>828-555-0142
      <svg viewBox="0 0 24 24"><path d="M6.6 10.8a15.1 15.1 0 0 0 6.6 6.6l2.2-2.2a1 1 0 0 1 1-.25 11.4 11.4 0 0 0 3.6.57 1 1 0 0 1 1 1V20a1 1 0 0 1-1 1A17 17 0 0 1 3 4a1 1 0 0 1 1-1h3.5a1 1 0 0 1 1 1c0 1.25.2 2.45.57 3.570a1 1 0 0 1-.25 1z"/></svg></li>
    <li>callum@mrtproperty.com
      <svg viewBox="0 0 24 24"><path d="M2 5h20v14H2z M3.5 6.5 12 13l8.5-6.5" stroke="var(--brand-navy)" stroke-width="1.6"/></svg></li>
    <li>www.mrtproperty.com
      <svg viewBox="0 0 24 24"><circle cx="12" cy="12" r="10"/><path d="M2 12h20M12 2c3 3 3 17 0 20M12 2c-3 3-3 17 0 20" stroke="var(--brand-navy)" stroke-width="1.4" fill="none"/></svg></li>
    <li>27 Harbour View Road Northmead<span class="spacer"></span></li>
  </ul>
</section>

</body>
</html>
```